I just need to get that same logo on the business card but with different word. “The Hinges Roadside and Rental”

Name: Marek T
Number: 4759028416
Email: thehingesroadside@brivomail.test

On the back, can we di just the logo and the hinges roadside and rental around it.

If possible a black card with the gold storefront type font that you used before, would be amazing. I attached the original logo just in case.

Target Market(s)

Roadside assistance

Industry/Entity Type

Repair/ roadside

Contact Information for Business Card

Name, email, phone number

Requirements
Must have
• Everything in description
Nice to have
• Nice big logo

```html
<!DOCTYPE html>
<html lang="en">
<head>
<meta charset="utf-8">
<title>The Hinges Roadside and Rental — Business Card</title>
<link rel="stylesheet" href="https://fonts.googleapis.com/css2?family=Montserrat:wght@400;700&display=swap">
<style>
  :root {
    --backdrop: #1e1e1f;
    --card: #121213;
    --card-edge: #262627;
    --gold: #b58d4c;
  }
  * { margin: 0; padding: 0; box-sizing: border-box; }
  html, body {
    width: 1200px;
    height: 857px;
    overflow: hidden;
    background: var(--backdrop);
    font-family: "Montserrat", sans-serif;
    color: var(--gold);
  }
  .canvas {
    position: relative;
    width: 1200px;
    height: 857px;
  }
  .card {
    position: absolute;
    width: 560px;
    height: 320px;
    background: var(--card);
    border: 1px solid var(--card-edge);
    border-radius: 4px;
    box-shadow: 0 18px 40px rgba(0, 0, 0, 0.45);
  }
  .card--back { left: 70px; top: 70px; }
  .card--front { left: 570px; top: 467px; }

  .brand {
    display: flex;
    align-items: center;
    gap: 18px;
    font-weight: 700;
  }
  .brand__mark {
    width: 46px;
    height: 46px;
    background: var(--gold);
    flex: none;
  }
  .brand__name {
    font-size: 38px;
    letter-spacing: 0.06em;
    line-height: 1;
    text-transform: uppercase;
  }
  .brand__tagline {
    display: block;
    margin-top: 8px;
    font-size: 13px;
    letter-spacing: 0.14em;
    text-transform: uppercase;
  }

  .card--back .brand {
    position: absolute;
    left: 50%;
    top: 50%;
    transform: translate(-50%, -50%);
  }

  .card--front .brand {
    position: absolute;
    left: 40px;
    bottom: 44px;
    flex-direction: column;
    align-items: flex-start;
    gap: 14px;
  }
  .card--front .brand__mark { width: 40px; height: 40px; }
  .card--front .brand__name { font-size: 30px; }
  .card--front .brand__tagline { font-size: 11px; }

  .contact {
    position: absolute;
    left: 300px;
    top: 70px;
  }
  .contact__name {
    font-weight: 700;
    font-size: 30px;
    letter-spacing: 0.08em;
    text-transform: uppercase;
    margin-bottom: 56px;
  }
  .contact__line {
    font-weight: 400;
    font-size: 14px;
    letter-spacing: 0.06em;
    margin-bottom: 14px;
  }
  .contact__line--email { font-size: 12px; letter-spacing: 0.03em; }
</style>
</head>
<body>
  <main class="canvas">
    <section class="card card--back" aria-label="Card back">
      <div class="brand">
        <span class="brand__mark" aria-hidden="true"></span>
        <div class="brand__name">The Hinges
          <span class="brand__tagline">Roadside and Rental</span>
        </div>
      </div>
    </section>

    <section class="card card--front" aria-label="Card front">
      <div class="brand">
        <span class="brand__mark" aria-hidden="true"></span>
        <div class="brand__name">The Hinges
          <span class="brand__tagline">Roadside and Rental</span>
        </div>
      </div>
      <div class="contact">
        <p class="contact__name">Marek T</p>
        <p class="contact__line">4759028416</p>
        <p class="contact__line contact__line--email">thehingesroadside@brivomail.test</p>
      </div>
    </section>
  </main>
</body>
</html>
```